My Pebble Porch Path Blog Re-Do Launch

I need a blog makeover. Someone started for me and they sold their company. The blog is primarily spiritual/inspirational. I would eventually like to monetize and launch some ebooks and/or other products. I am open to suggestions. I am learning as we go along, so please keep that in mind. The final design should be warm and welcoming. I am open to suggestions. I am looking to build a relationship.

Target Market(s)

women, moms, females with chronic health issues, moms of special needs kids, those who need encouragement

Industry/Entity Type

Religious

Number of Pages Required

4 page

Font styles to use
Sans Serif

Colors
eddcec
fdf9cf
ffffff

Requirements
Must have
• I would like my main page to have a short about section, relevant posts, recent posts, and archive posts. The main page should also have a place to subscribe as well a search feature.
Nice to have
• Buttons (grab my button), blogs I follow, e-cart capabilities

```html
<!DOCTYPE html>
<html lang="en">
<head>
<meta charset="utf-8">
<title>My Pebble Porch Path</title>
<link rel="stylesheet" href="https://fonts.googleapis.com/css2?family=Bitter:wght@400;500&family=Roboto:ital,wght@0,400;0,500;1,400&display=swap">
<style>
:root{
  --pink:#eddcec;
  --pink-deep:#dcc3db;
  --cream:#fdf9cf;
  --cream-line:#eee49a;
  --white:#ffffff;
  --ink:#1f1f1f;
  --text:#555555;
  --muted:#9a9a9a;
  --meta-icon:#e2c98e;
  --line:#e6e6e6;
  --footer:#1b1b1b;
  --orange:#e8642c;
}
*{box-sizing:border-box;margin:0;padding:0}
html,body{width:1200px;height:2270px;overflow:hidden;background:var(--white)}
body{position:relative;font-family:'Roboto',Arial,sans-serif;color:var(--text)}
.serif{font-family:'Bitter',Georgia,serif}

/* top bar */
.topbar{position:absolute;left:0;top:0;width:1200px;height:68px;background:var(--pink)}
.search{position:absolute;left:691px;top:20px;width:324px;height:33px;display:flex}
.search-field{flex:1;background:var(--white);font-size:12px;font-style:italic;color:#b5b5b5;padding:9px 14px}
.search-btn{width:36px;background:var(--pink-deep);display:flex;align-items:center;justify-content:center}
.user-name{position:absolute;left:1038px;top:27px;font-size:13px;font-weight:500;color:var(--ink)}
.user-avatar{position:absolute;left:1080px;top:14px;width:42px;height:42px;border-radius:50%;background:linear-gradient(135deg,#d9d2cb,#8a7f77)}

/* brand ribbon */
.brand{position:absolute;left:80px;top:0;width:121px;height:220px;z-index:3}
.brand svg{position:absolute;left:0;top:0}
.brand-mark{position:absolute;left:48px;top:48px;width:24px;height:24px;border-radius:50%;background:#c9a24a}
.brand-name{position:absolute;left:6px;top:110px;width:109px;text-align:center;font-family:'Bitter',Georgia,serif;font-size:16px;line-height:21px;color:var(--ink)}

/* navigation */
.nav{position:absolute;left:0;top:68px;width:1200px;height:58px;background:var(--white)}
.nav ul{list-style:none;position:absolute;top:0;left:0;height:58px;width:1200px}
.nav li{position:absolute;top:22px;font-family:'Bitter',Georgia,serif;font-size:14px;color:var(--ink)}
.nav li.active{color:#bdbdbd}
.nav li.active::before{content:"";position:absolute;left:-12px;right:-12px;top:-22px;height:4px;background:var(--pink)}
.nav li.active::after{content:"";position:absolute;left:50%;top:-18px;margin-left:-7px;border:7px solid transparent;border-top-color:var(--pink)}
.nav li + li::before{content:"";position:absolute;left:-16px;top:0;width:1px;height:18px;background:var(--line)}
.nav li.active + li::before{display:none}

/* hero */
.hero{position:absolute;left:0;top:126px;width:1200px;height:562px;background:radial-gradient(ellipse 420px 300px at 870px 420px,#fff2c2 0%,#f9c773 35%,rgba(233,140,60,0) 75%),linear-gradient(180deg,#7a8792 0%,#b7a58d 30%,#e6a865 60%,#d77a3a 100%)}
.hero-title{position:absolute;left:133px;top:185px;font-family:'Bitter',Georgia,serif;font-size:55px;line-height:60px;color:#161616;font-weight:400}
.hero-title span{display:block;font-size:42px;line-height:52px}
.hero-text{position:absolute;left:133px;top:322px;width:390px;font-size:15px;line-height:21px;font-style:italic;color:#222;text-align:justify}
.hero-arrow{position:absolute;top:258px;width:56px;height:56px;border-radius:50%;background:var(--white);border:4px solid #d7c7a8;display:flex;align-items:center;justify-content:center}
.hero-arrow.prev{left:40px}
.hero-arrow.next{left:1104px}

/* posts */
.relevant{position:absolute;left:76px;top:750px;width:770px}
.section-bar{height:43px;background:var(--cream);border-left:3px solid var(--cream-line);font-family:'Bitter',Georgia,serif;font-size:18px;color:var(--ink);padding:11px 16px}
.post{height:203px;border:1px solid var(--line);margin-top:21px;padding:20px 22px 0 15px;display:flex;position:relative}
.post + .post{margin-top:21px}
.post-image{width:194px;height:165px;flex:none}
.post-body{margin-left:24px;flex:1}
.post-title{font-family:'Bitter',Georgia,serif;font-size:18px;font-weight:400;color:var(--ink);margin-top:2px}
.post-text{font-size:12.4px;line-height:21px;text-align:justify;margin-top:8px;color:#4a4a4a}
.post-meta{position:absolute;left:233px;top:167px;display:flex;font-size:12px;color:var(--muted)}
.post-meta span{display:flex;align-items:center;gap:6px;margin-right:30px}
.post-meta span:nth-child(2){margin-right:48px}
.post-meta span:nth-child(3){margin-right:40px}

/* sidebar */
.newsletter{position:absolute;left:884px;top:750px;width:242px;height:261px;background:var(--pink);padding:19px 20px}
.side-title{font-family:'Bitter',Georgia,serif;font-size:17px;color:var(--ink);font-weight:400}
.newsletter p{font-size:12.5px;line-height:19px;color:#8a8a8a;margin-top:8px}
.field{height:32px;background:var(--white);margin-top:10px;font-size:12px;color:#aaa;padding:9px 10px;margin-left:0}
.newsletter .field:first-of-type{margin-top:18px}
.submit{height:40px;background:var(--pink-deep);margin-top:12px;color:var(--white);font-size:11px;font-weight:500;letter-spacing:.5px;text-align:center;padding-top:13px}

.recent{position:absolute;left:884px;top:1047px;width:242px}
.recent .side-title{font-size:20px}
.recent-item{display:flex;padding:18px 0 14px;border-bottom:1px solid var(--line);height:121px}
.recent-item:first-of-type{padding-top:15px}
.recent-item:last-child{border-bottom:none}
.recent-thumb{width:76px;height:65px;flex:none}
.recent-info{margin-left:18px}
.recent-info p{font-size:12.5px;line-height:21px;text-align:justify;color:#4a4a4a}
.counts{display:flex;gap:18px;font-size:12px;color:#666;margin-top:6px}
.counts span{display:flex;align-items:center;gap:5px}

.archive{position:absolute;left:884px;top:1469px;width:242px;height:298px;background:var(--cream);padding:16px 20px}
.archive .side-title{font-size:20px}
.archive-item{display:flex;gap:16px;padding:14px 0 12px;border-bottom:1px dashed #e2da9e}
.archive-item:last-child{border-bottom:none}
.archive-item p{font-size:12.5px;line-height:20px;color:#333}

.follow{position:absolute;left:884px;top:1800px;width:242px}
.follow .side-title{font-size:20px}
.follow-item{display:flex;gap:16px;padding:18px 0 16px;border-bottom:1px dashed var(--line)}
.follow-item:last-child{border-bottom:none}
.follow-icon{width:32px;height:32px;border-radius:7px;background:var(--orange);flex:none;margin-top:3px}
.follow-item p{font-size:12.8px;line-height:19px;text-align:justify;color:#333}

/* footer */
.footer{position:absolute;left:0;top:2197px;width:1200px;height:73px;background:var(--footer)}
.copyright{position:absolute;left:77px;top:29px;font-size:12px;color:#8a8a8a}
.social{position:absolute;left:985px;top:24px;display:flex;gap:9px}
.social span{width:26px;height:26px;background:#6f7d8c;display:block}
</style>
</head>
<body>

<header>
  <div class="topbar">
    <div class="search">
      <div class="search-field">Search here...</div>
      <div class="search-btn">
        <svg width="14" height="14" viewBox="0 0 14 14"><circle cx="6" cy="6" r="4.5" fill="none" stroke="#fff" stroke-width="2"/><line x1="9.3" y1="9.3" x2="13" y2="13" stroke="#fff" stroke-width="2"/></svg>
      </div>
    </div>
    <div class="user-name">MARA</div>
    <div class="user-avatar" role="img" aria-label="Member profile photo"></div>
  </div>

  <div class="brand">
    <svg width="121" height="220" viewBox="0 0 121 220"><path d="M0 0H121V190L60.5 220L0 190Z" fill="#fff"/><path d="M0 0V190" stroke="#e5e5e5"/><path d="M121 0V190" stroke="#e5e5e5"/></svg>
    <div class="brand-mark"></div>
    <div class="brand-name">My Pebble Porch Path</div>
  </div>

  <nav class="nav">
    <ul>
      <li class="active" style="left:401px">Home</li>
      <li style="left:480px">About</li>
      <li style="left:557px">Sessions</li>
      <li style="left:660px">Starting Out</li>
      <li style="left:782px">Community</li>
      <li style="left:906px">Contact</li>
      <li style="left:1003px">Spirituality eBook</li>
    </ul>
  </nav>
</header>

<section class="hero" role="img" aria-label="Raised open hands against a golden sunset sky">
  <h1 class="hero-title">My<span>Pebble Porch Path</span></h1>
  <p class="hero-text">Ut enim ad minim veniam, quis nostrud exercitation ullamco laboris nisi ut aliquip ex ea commodo consequat. Duis aute irure dolor in reprehenderit.</p>
  <div class="hero-arrow prev"><svg width="14" height="18" viewBox="0 0 14 18"><path d="M10 2L3 9l7 7" fill="none" stroke="#222" stroke-width="2.4"/></svg></div>
  <div class="hero-arrow next"><svg width="14" height="18" viewBox="0 0 14 18"><path d="M4 2l7 7-7 7" fill="none" stroke="#222" stroke-width="2.4"/></svg></div>
</section>

<main class="relevant">
  <h2 class="section-bar">Relevant Posts</h2>

  <article class="post">
    <div class="post-image" role="img" aria-label="Woman praying at a sunset shore" style="background:linear-gradient(160deg,#7d7370,#e9a57c 55%,#433b3c)"></div>
    <div class="post-body">
      <h3 class="post-title">de Finibus Bonorum et Malorum</h3>
      <p class="post-text">Lorem ipsum dolor sit amet, consectetur adipiscing elit, sed do eiusmod tempor incididunt ut labore et dolore magna aliqua. Ut enim ad minim veniam, quis nostrud exercitation ullamco laboris nisi ut aliquip ex ea commodo consequat. Duis aute irure dolor in reprehenderit in voluptate velit esse cillum dolore.</p>
    </div>
    <div class="post-meta">
      <span><svg width="10" height="11" viewBox="0 0 10 11"><circle cx="5" cy="3" r="2.6" fill="#e2c98e"/><path d="M0 11c0-3.5 2-5 5-5s5 1.5 5 5z" fill="#e2c98e"/></svg>Post by Admin</span>
      <span><svg width="13" height="11" viewBox="0 0 13 11"><ellipse cx="6.5" cy="5" rx="6.5" ry="4.6" fill="#e2c98e"/><path d="M2 8l-1 3 4-2z" fill="#e2c98e"/></svg>Comments</span>
      <span><svg width="11" height="11" viewBox="0 0 11 11"><path d="M1 5h2v6H1zM4 5l2-5c1.5 0 2 1 1.5 3H10l-1 8H4z" fill="none" stroke="#e2c98e"/></svg>Likes</span>
      <span><svg width="11" height="11" viewBox="0 0 11 11"><circle cx="9" cy="2" r="1.8" fill="#e2c98e"/><circle cx="2" cy="5.5" r="1.8" fill="#e2c98e"/><circle cx="9" cy="9" r="1.8" fill="#e2c98e"/><path d="M9 2L2 5.5 9 9" fill="none" stroke="#e2c98e"/></svg>Share</span>
    </div>
  </article>

  <article class="post">
    <div class="post-image" role="img" aria-label="Hand reaching toward spring blossoms" style="background:linear-gradient(170deg,#eceaf0,#d8cbb8 45%,#8c8a3b)"></div>
    <div class="post-body">
      <h3 class="post-title">de Finibus Bonorum et Malorum</h3>
      <p class="post-text">Lorem ipsum dolor sit amet, consectetur adipiscing elit, sed do eiusmod tempor incididunt ut labore et dolore magna aliqua. Ut enim ad minim veniam, quis nostrud exercitation ullamco laboris nisi ut aliquip ex ea commodo consequat. Duis aute irure dolor in reprehenderit in voluptate velit esse cillum dolore.</p>
    </div>
    <div class="post-meta">
      <span><svg width="10" height="11" viewBox="0 0 10 11"><circle cx="5" cy="3" r="2.6" fill="#e2c98e"/><path d="M0 11c0-3.5 2-5 5-5s5 1.5 5 5z" fill="#e2c98e"/></svg>Post by Admin</span>
      <span><svg width="13" height="11" viewBox="0 0 13 11"><ellipse cx="6.5" cy="5" rx="6.5" ry="4.6" fill="#e2c98e"/><path d="M2 8l-1 3 4-2z" fill="#e2c98e"/></svg>Comments</span>
      <span><svg width="11" height="11" viewBox="0 0 11 11"><path d="M1 5h2v6H1zM4 5l2-5c1.5 0 2 1 1.5 3H10l-1 8H4z" fill="none" stroke="#e2c98e"/></svg>Likes</span>
      <span><svg width="11" height="11" viewBox="0 0 11 11"><circle cx="9" cy="2" r="1.8" fill="#e2c98e"/><circle cx="2" cy="5.5" r="1.8" fill="#e2c98e"/><circle cx="9" cy="9" r="1.8" fill="#e2c98e"/><path d="M9 2L2 5.5 9 9" fill="none" stroke="#e2c98e"/></svg>Share</span>
    </div>
  </article>

  <article class="post">
    <div class="post-image" role="img" aria-label="Feathered dream catcher against a teal sky" style="background:linear-gradient(150deg,#2a6f74,#6fa7a0 50%,#b8b49a)"></div>
    <div class="post-body">
      <h3 class="post-title">de Finibus Bonorum et Malorum</h3>
      <p class="post-text">Lorem ipsum dolor sit amet, consectetur adipiscing elit, sed do eiusmod tempor incididunt ut labore et dolore magna aliqua. Ut enim ad minim veniam, quis nostrud exercitation ullamco laboris nisi ut aliquip ex ea commodo consequat. Duis aute irure dolor in reprehenderit in voluptate velit esse cillum dolore.</p>
    </div>
    <div class="post-meta">
      <span><svg width="10" height="11" viewBox="0 0 10 11"><circle cx="5" cy="3" r="2.6" fill="#e2c98e"/><path d="M0 11c0-3.5 2-5 5-5s5 1.5 5 5z" fill="#e2c98e"/></svg>Post by Admin</span>
      <span><svg width="13" height="11" viewBox="0 0 13 11"><ellipse cx="6.5" cy="5" rx="6.5" ry="4.6" fill="#e2c98e"/><path d="M2 8l-1 3 4-2z" fill="#e2c98e"/></svg>Comments</span>
      <span><svg width="11" height="11" viewBox="0 0 11 11"><path d="M1 5h2v6H1zM4 5l2-5c1.5 0 2 1 1.5 3H10l-1 8H4z" fill="none" stroke="#e2c98e"/></svg>Likes</span>
      <span><svg width="11" height="11" viewBox="0 0 11 11"><circle cx="9" cy="2" r="1.8" fill="#e2c98e"/><circle cx="2" cy="5.5" r="1.8" fill="#e2c98e"/><circle cx="9" cy="9" r="1.8" fill="#e2c98e"/><path d="M9 2L2 5.5 9 9" fill="none" stroke="#e2c98e"/></svg>Share</span>
    </div>
  </article>

  <article class="post">
    <div class="post-image" role="img" aria-label="Praying hands lit by warm sunlight" style="background:radial-gradient(circle at 50% 45%,#fff6d0,#f3b955 45%,#b56a2c)"></div>
    <div class="post-body">
      <h3 class="post-title">de Finibus Bonorum et Malorum</h3>
      <p class="post-text">Lorem ipsum dolor sit amet, consectetur adipiscing elit, sed do eiusmod tempor incididunt ut labore et dolore magna aliqua. Ut enim ad minim veniam, quis nostrud exercitation ullamco laboris nisi ut aliquip ex ea commodo consequat. Duis aute irure dolor in reprehenderit in voluptate velit esse cillum dolore.</p>
    </div>
    <div class="post-meta">
      <span><svg width="10" height="11" viewBox="0 0 10 11"><circle cx="5" cy="3" r="2.6" fill="#e2c98e"/><path d="M0 11c0-3.5 2-5 5-5s5 1.5 5 5z" fill="#e2c98e"/></svg>Post by Admin</span>
      <span><svg width="13" height="11" viewBox="0 0 13 11"><ellipse cx="6.5" cy="5" rx="6.5" ry="4.6" fill="#e2c98e"/><path d="M2 8l-1 3 4-2z" fill="#e2c98e"/></svg>Comments</span>
      <span><svg width="11" height="11" viewBox="0 0 11 11"><path d="M1 5h2v6H1zM4 5l2-5c1.5 0 2 1 1.5 3H10l-1 8H4z" fill="none" stroke="#e2c98e"/></svg>Likes</span>
      <span><svg width="11" height="11" viewBox="0 0 11 11"><circle cx="9" cy="2" r="1.8" fill="#e2c98e"/><circle cx="2" cy="5.5" r="1.8" fill="#e2c98e"/><circle cx="9" cy="9" r="1.8" fill="#e2c98e"/><path d="M9 2L2 5.5 9 9" fill="none" stroke="#e2c98e"/></svg>Share</span>
    </div>
  </article>

  <article class="post">
    <div class="post-image" role="img" aria-label="Woman silhouetted against an evening sunset" style="background:linear-gradient(180deg,#6c5f80,#e08a5a 45%,#3a2f3d)"></div>
    <div class="post-body">
      <h3 class="post-title">de Finibus Bonorum et Malorum</h3>
      <p class="post-text">Lorem ipsum dolor sit amet, consectetur adipiscing elit, sed do eiusmod tempor incididunt ut labore et dolore magna aliqua. Ut enim ad minim veniam, quis nostrud exercitation ullamco laboris nisi ut aliquip ex ea commodo consequat. Duis aute irure dolor in reprehenderit in voluptate velit esse cillum dolore.</p>
    </div>
    <div class="post-meta">
      <span><svg width="10" height="11" viewBox="0 0 10 11"><circle cx="5" cy="3" r="2.6" fill="#e2c98e"/><path d="M0 11c0-3.5 2-5 5-5s5 1.5 5 5z" fill="#e2c98e"/></svg>Post by Admin</span>
      <span><svg width="13" height="11" viewBox="0 0 13 11"><ellipse cx="6.5" cy="5" rx="6.5" ry="4.6" fill="#e2c98e"/><path d="M2 8l-1 3 4-2z" fill="#e2c98e"/></svg>Comments</span>
      <span><svg width="11" height="11" viewBox="0 0 11 11"><path d="M1 5h2v6H1zM4 5l2-5c1.5 0 2 1 1.5 3H10l-1 8H4z" fill="none" stroke="#e2c98e"/></svg>Likes</span>
      <span><svg width="11" height="11" viewBox="0 0 11 11"><circle cx="9" cy="2" r="1.8" fill="#e2c98e"/><circle cx="2" cy="5.5" r="1.8" fill="#e2c98e"/><circle cx="9" cy="9" r="1.8" fill="#e2c98e"/><path d="M9 2L2 5.5 9 9" fill="none" stroke="#e2c98e"/></svg>Share</span>
    </div>
  </article>

  <article class="post">
    <div class="post-image" role="img" aria-label="Person meditating by the sea in bright light" style="background:linear-gradient(170deg,#d8d4b0,#b8c0a4 45%,#3f6a6f)"></div>
    <div class="post-body">
      <h3 class="post-title">de Finibus Bonorum et Malorum</h3>
      <p class="post-text">Lorem ipsum dolor sit amet, consectetur adipiscing elit, sed do eiusmod tempor incididunt ut labore et dolore magna aliqua. Ut enim ad minim veniam, quis nostrud exercitation ullamco laboris nisi ut aliquip ex ea commodo consequat. Duis aute irure dolor in reprehenderit in voluptate velit esse cillum dolore.</p>
    </div>
    <div class="post-meta">
      <span><svg width="10" height="11" viewBox="0 0 10 11"><circle cx="5" cy="3" r="2.6" fill="#e2c98e"/><path d="M0 11c0-3.5 2-5 5-5s5 1.5 5 5z" fill="#e2c98e"/></svg>Post by Admin</span>
      <span><svg width="13" height="11" viewBox="0 0 13 11"><ellipse cx="6.5" cy="5" rx="6.5" ry="4.6" fill="#e2c98e"/><path d="M2 8l-1 3 4-2z" fill="#e2c98e"/></svg>Comments</span>
      <span><svg width="11" height="11" viewBox="0 0 11 11"><path d="M1 5h2v6H1zM4 5l2-5c1.5 0 2 1 1.5 3H10l-1 8H4z" fill="none" stroke="#e2c98e"/></svg>Likes</span>
      <span><svg width="11" height="11" viewBox="0 0 11 11"><circle cx="9" cy="2" r="1.8" fill="#e2c98e"/><circle cx="2" cy="5.5" r="1.8" fill="#e2c98e"/><circle cx="9" cy="9" r="1.8" fill="#e2c98e"/><path d="M9 2L2 5.5 9 9" fill="none" stroke="#e2c98e"/></svg>Share</span>
    </div>
  </article>
</main>

<aside>
  <section class="newsletter">
    <h3 class="side-title">Subscribe Newsletter</h3>
    <p>Ut enim ad minim veniam, quis nostrud exercitation</p>
    <div class="field">Name:*</div>
    <div class="field">Email:*</div>
    <div class="submit">SUBMIT HERE</div>
  </section>

  <section class="recent">
    <h3 class="side-title">Recent Posts</h3>
    <div class="recent-item">
      <div class="recent-thumb" role="img" aria-label="Lone tree at golden sunset" style="background:linear-gradient(180deg,#e9a64e,#8a4b1e)"></div>
      <div class="recent-info">
        <p>Ut enim situ ead minim veniam, quis nostrud exercitationp</p>
        <div class="counts">
          <span><svg width="12" height="10" viewBox="0 0 13 11"><ellipse cx="6.5" cy="5" rx="6.5" ry="4.6" fill="#d9b8d8"/><path d="M2 8l-1 3 4-2z" fill="#d9b8d8"/></svg>(12)</span>
          <span><svg width="11" height="11" viewBox="0 0 11 11"><path d="M1 5h2v6H1zM4 5l2-5c1.5 0 2 1 1.5 3H10l-1 8H4z" fill="none" stroke="#aaa"/></svg>(3)</span>
        </div>
      </div>
    </div>
    <div class="recent-item">
      <div class="recent-thumb" role="img" aria-label="Golden statue in a dark temple" style="background:linear-gradient(135deg,#1d1a14,#a7762b 55%,#2a231a)"></div>
      <div class="recent-info">
        <p>Ut enim situ ead minim veniam, quis nostrud exercitationp</p>
        <div class="counts">
          <span><svg width="12" height="10" viewBox="0 0 13 11"><ellipse cx="6.5" cy="5" rx="6.5" ry="4.6" fill="#d9b8d8"/><path d="M2 8l-1 3 4-2z" fill="#d9b8d8"/></svg>(12)</span>
          <span><svg width="11" height="11" viewBox="0 0 11 11"><path d="M1 5h2v6H1zM4 5l2-5c1.5 0 2 1 1.5 3H10l-1 8H4z" fill="none" stroke="#aaa"/></svg>(3)</span>
        </div>
      </div>
    </div>
    <div class="recent-item">
      <div class="recent-thumb" role="img" aria-label="Soft pastel sky over water" style="background:linear-gradient(180deg,#f1d7c6,#a9c4d6)"></div>
      <div class="recent-info">
        <p>Ut enim situ ead minim veniam, quis nostrud exercitationp</p>
        <div class="counts">
          <span><svg width="12" height="10" viewBox="0 0 13 11"><ellipse cx="6.5" cy="5" rx="6.5" ry="4.6" fill="#d9b8d8"/><path d="M2 8l-1 3 4-2z" fill="#d9b8d8"/></svg>(12)</span>
          <span><svg width="11" height="11" viewBox="0 0 11 11"><path d="M1 5h2v6H1zM4 5l2-5c1.5 0 2 1 1.5 3H10l-1 8H4z" fill="none" stroke="#aaa"/></svg>(3)</span>
        </div>
      </div>
    </div>
  </section>

  <section class="archive">
    <h3 class="side-title">Archive Posts</h3>
    <div class="archive-item">
      <svg width="24" height="18" viewBox="0 0 24 18" style="flex:none;margin-top:2px"><rect x="1" y="4" width="22" height="13" fill="none" stroke="#222" stroke-width="1.4"/><path d="M1 4l11 8 11-8M1 17l8-7M23 17l-8-7M4 4l4-3h8l4 3" fill="none" stroke="#222" stroke-width="1.4"/></svg>
      <p>Lorem ipsum dolor sit amet, consectetur adipiscing elit, sed do eiusmod.</p>
    </div>
    <div class="archive-item">
      <svg width="24" height="18" viewBox="0 0 24 18" style="flex:none;margin-top:2px"><rect x="1" y="4" width="22" height="13" fill="none" stroke="#222" stroke-width="1.4"/><path d="M1 4l11 8 11-8M1 17l8-7M23 17l-8-7M4 4l4-3h8l4 3" fill="none" stroke="#222" stroke-width="1.4"/></svg>
      <p>Lorem ipsum dolor sit amet, consectetur adipiscing elit, sed do eiusmod.</p>
    </div>
    <div class="archive-item">
      <svg width="24" height="18" viewBox="0 0 24 18" style="flex:none;margin-top:2px"><rect x="1" y="4" width="22" height="13" fill="none" stroke="#222" stroke-width="1.4"/><path d="M1 4l11 8 11-8M1 17l8-7M23 17l-8-7M4 4l4-3h8l4 3" fill="none" stroke="#222" stroke-width="1.4"/></svg>
      <p>Lorem ipsum dolor sit amet, consectetur adipiscing elit, sed do eiusmod.</p>
    </div>
  </section>

  <section class="follow">
    <h3 class="side-title">Blogs I follow</h3>
    <div class="follow-item"><span class="follow-icon"></span><p>Lorem ipsum dolor sit amet, consectetur adipiscing elit, sed do eiusmod tempor.</p></div>
    <div class="follow-item"><span class="follow-icon"></span><p>Lorem ipsum dolor sit amet, consectetur adipiscing elit, sed do eiusmod tempor.</p></div>
    <div class="follow-item"><span class="follow-icon"></span><p>Lorem ipsum dolor sit amet, consectetur adipiscing elit, sed do eiusmod tempor.</p></div>
  </section>
</aside>

<footer class="footer">
  <p class="copyright">© 2015, Yoursite, All Right Reserved.</p>
  <div class="social"><span></span><span></span><span></span><span></span></div>
</footer>

</body>
</html>
```